Webdesign für Kleingruppenreisen in die Südsteiermark
Zielgruppe
Wir sind ein Start-Up Unternehmen, das als Kleingruppenreisen in die Südsteiermark veranstaltet; der Schwerpunkt liegt auf dem Kulinarischen. Zielgruppe sind Geschäftsleute, die diese Kurzreisen (Do-So) für Marketingzwecke oder als Mitarbeiterbonus (oder auch privat) nutzen möchten.
Aufgabenstellung
Die Homepage soll eine Online-Shop Möglichkeit bieten, in der die Reise (bisher gibt es nur einen Ablauf) gebucht werden kann. Optisch sollte sie sich an das bereits von Ihnen erstellte Logo anlehnen und möglichst ansprechende Fotos von der Südsteiermark, Graz, Leoben usw. enthalten. (Siehe die beiden Flyer und das Logo)
Wir haben inzwischen Bildfreigaben von Haldauer und dem Tourismusverband Kellwinden erhalten und können auch eigene Bilder zur Verfügung stellen. Bitte kontaktieren Sie uns dafür, wenn nötig.

```html
<!DOCTYPE html>
<html lang="de">
<head>
<meta charset="utf-8">
<title>GaumenpfadReisen – Reisen für Feinschmecker</title>
<link href="https://fonts.googleapis.com/css2?family=Open+Sans:ital,wght@0,300;0,400;0,600;0,700;1,600;1,700&family=Yesteryear&display=swap" rel="stylesheet">
<style>
:root{
  --red:#a51c29;
  --red-dark:#8d1521;
  --grey:#ededed;
  --text:#333;
  --white:#fff;
  --leaf:#8fae2c;
  --sans:'Open Sans', Arial, sans-serif;
  --script:'Yesteryear', cursive;
}
*{margin:0;padding:0;box-sizing:border-box}
html,body{width:678px;height:1200px;overflow:hidden;background:var(--white)}
body{position:relative;font-family:var(--sans);color:var(--text)}
.abs{position:absolute}

/* hero */
.hero{left:0;top:0;width:678px;height:247px;
  background:linear-gradient(180deg,#c9cdc8 0%,#b9c2b4 22%,#6f8d3e 45%,#54762a 70%,#3c5a1d 100%)}
.hero-left{left:0;top:0;width:160px;height:247px;background:linear-gradient(135deg,#4f6d22,#2f3d1e 60%,#3d4a2a)}
.logo-box{left:128px;top:0;width:137px;height:82px;background:var(--white);display:flex;align-items:center;justify-content:center;gap:5px}
.logo-dot{width:8px;height:8px;border-radius:50%;background:var(--red)}
.logo-name{font-size:11px;font-weight:700;color:var(--red)}
.nav{left:265px;top:50px;width:285px;height:20px;background:var(--red);display:flex;align-items:center;padding-left:48px;gap:9px}
.nav a{color:var(--white);font-size:6.6px;font-weight:600;text-decoration:none}
.caption{left:128px;background:rgba(165,28,41,.85);color:var(--white);font-size:13px;line-height:28px;padding:0 5px}
.dots{top:238px;left:324px;display:flex;gap:8px}
.dots span{width:4px;height:4px;background:#ccc}
.dots span.on{background:var(--red)}

/* headings */
.script-title{width:678px;left:0;text-align:center;font-family:var(--script);color:var(--red);font-size:22px}
.divider{left:305px;width:68px;height:6px}
.divider::before{content:"";position:absolute;left:0;right:0;top:3px;border-top:.6px solid #555}
.divider::after{content:"";position:absolute;left:29px;top:0;width:8px;height:7px;border-radius:50%;background:var(--leaf)}

.intro{left:139px;top:315px;width:400px;text-align:center;font-size:6.3px;line-height:7.6px}
.btn{background:var(--red);color:var(--white);text-align:center;font-size:8.6px}

/* tours */
.tours{left:0;top:422px;width:678px;height:235px;background:var(--grey)}
.card{top:480px;width:124px;height:88px;box-shadow:0 0 2px rgba(0,0,0,.3)}
.card-img{position:absolute;left:0;top:0;width:124px;height:62px}
.card-label{position:absolute;left:0;top:61px;width:124px;height:27px;background:rgba(165,28,41,.92);color:var(--white);font-size:10.5px;line-height:27px;text-align:center}
.card-text{top:578px;width:124px;text-align:center;font-size:6.2px;line-height:7.6px}

/* call to action */
.cta{left:0;top:657px;width:678px;height:166px;background:linear-gradient(120deg,#a33038 0%,#b8454a 35%,#a5363d 60%,#8f2630 100%)}
.cta-title{left:130px;top:679px;color:var(--white);font-size:16px;font-weight:700;font-style:italic;line-height:21px}
.cta-sub{left:130px;top:742px;color:var(--white);font-size:12.5px;font-weight:300;line-height:15.5px}
.cta-btn{left:391px;top:766px;width:162px;height:25px;border:.8px solid var(--white);color:var(--white);font-size:12.5px;font-style:italic;font-weight:600;text-align:center;line-height:23px}

/* feature */
.feature-img{left:128px;top:861px;width:207px;height:139px;background:linear-gradient(180deg,#8cb4e0 0%,#c0603e 40%,#d08a4e 65%,#7a7a80 100%)}
.arrow{top:915px;width:21px;height:21px;border-radius:50%;background:#e6e6e6;display:flex;align-items:center;justify-content:center}
.feature-head{left:345px;top:854px;font-family:var(--script);color:var(--red);font-size:17px}
.feature-text{left:345px;width:205px;font-size:6px;line-height:7.6px;font-weight:300;color:#444}
.price{left:342px;top:953px;font-family:var(--script);color:var(--red);font-size:17px}

/* footer */
.skyline{left:0;top:1016px;width:312px;height:70px;background:linear-gradient(180deg,rgba(165,28,41,.15),rgba(165,28,41,.7) 60%,var(--red))}
.footer{left:0;top:1086px;width:678px;height:114px;background:var(--red);color:var(--white)}
.f-text{font-size:6.4px;line-height:7.8px;color:var(--white)}
.f-brand{font-family:var(--script);font-size:9px}
.f-col h4{font-size:6.4px;font-weight:700;margin-bottom:5px}
.f-col p{font-size:6.3px;margin-bottom:4.5px}
.social{top:1109px;width:28px;height:28px;border-radius:50%;background:var(--white)}
.f-rule{left:128px;top:1173px;width:422px;border-top:.6px solid rgba(255,255,255,.8)}
.copy{left:0;top:1180px;width:678px;text-align:center;font-size:6.3px;color:var(--white)}
</style>
</head>
<body>

<header>
  <div class="abs hero" role="img" aria-label="Foto: Weinberge der Südsteiermark mit Trauben im Vordergrund"></div>
  <div class="abs hero-left" role="img" aria-label="Foto: dunkle Weintrauben am Rebstock"></div>
  <div class="abs logo-box"><span class="logo-dot"></span><span class="logo-name">GaumenpfadReisen</span></div>
  <nav class="abs nav">
    <a>Startseite</a><a>Jetzt buchen</a><a>Shop</a><a>Kontakt</a><a>Ein Menüpunkt</a>
  </nav>
  <div class="abs caption" style="top:151px">Lorem Ipsum dolor</div>
  <div class="abs caption" style="top:187px">consetetur sadipscing elitr, sed</div>
  <div class="abs dots"><span></span><span class="on"></span><span></span></div>
</header>

<section>
  <h1 class="abs script-title" style="top:262px">Herzlich Willkommen</h1>
  <div class="abs divider" style="top:295px"></div>
  <p class="abs intro">Wir lieben die Steiermark mit ihrem guten Essen, hervorragendem Bier und exquisitem Wein und möchten gerne anspruchsvolle Gäste verwöhnen. Als Start-up Unternehmen mit Sitz in Berlin und wollen wir unsere Begeisterung für die Steiermark mit ihren kulinarischen Spezialitäten, wunderschönen Landschaften und gastfreundlichen Menschen gern mit unseren Gästen teilen. „GaumenpfadReisen“ ist daher auf der Suche nach Partnern, die mit uns unser neues Projekt in der Steiermark starten möchten.</p>
  <div class="abs btn" style="left:299px;top:365px;width:77px;height:21px;line-height:21px">mehr Erfahren</div>
</section>

<section>
  <div class="abs tours"></div>
  <h2 class="abs script-title" style="top:426px">GaumenpfadReisen</h2>
  <div class="abs divider" style="top:460px"></div>

  <div class="abs card" style="left:128px">
    <div class="card-img" role="img" aria-label="Foto: Weinberg mit Hügellandschaft" style="background:linear-gradient(180deg,#8fb8e8,#5d7a3a 60%,#3e5a22)"></div>
    <div class="card-label">Vom Bier zum Wein</div>
  </div>
  <div class="abs card" style="left:277px">
    <div class="card-img" role="img" aria-label="Foto: Rebhang unter Wolkenhimmel" style="background:linear-gradient(180deg,#6fa3df,#dfe9f2 35%,#6a7f45 65%,#3e5424)"></div>
    <div class="card-label">lorem Ipsum</div>
  </div>
  <div class="abs card" style="left:427px">
    <div class="card-img" role="img" aria-label="Foto: Bergsee mit Felswand" style="background:linear-gradient(180deg,#6c8fb8,#3d5a3a 40%,#4c8fb0 65%,#a7c6cf)"></div>
    <div class="card-label">lorem Ipsum</div>
  </div>

  <p class="abs card-text" style="left:128px">Lernen Sie Leoben, die Hauptstadt des Haldauer-Bieres kennen  und erfahren Sie im Haldauerium die Geschichte dieses weltbekannten Gebräus.</p>
  <p class="abs card-text" style="left:277px">Lorem ipsum dolor sit amet, consetetur sadipscing elitr, sed diam nonumy eirmod tempor invidunta.</p>
  <p class="abs card-text" style="left:427px">Lorem ipsum dolor sit amet, consetetur sadipscing elitr, sed diam nonumy eirmod tempor invidunta.</p>

  <div class="abs btn" style="left:150px;top:614px;width:78px;height:21px;line-height:21px">mehr Erfahren</div>
  <div class="abs btn" style="left:300px;top:614px;width:78px;height:21px;line-height:21px">mehr Erfahren</div>
  <div class="abs btn" style="left:450px;top:614px;width:78px;height:21px;line-height:21px">mehr Erfahren</div>
</section>

<section>
  <div class="abs cta" role="img" aria-label="Foto: Weintrauben mit roter Farbfläche überlagert"></div>
  <h2 class="abs cta-title">Erleben Sie die<br>gastronomische Vielfalt der Süd-Steiermark</h2>
  <p class="abs cta-sub">Sie suchen ein bestimmtes Gaumenerlebnis?<br>Dann helfen wir Ihnen gerne weiter.</p>
  <div class="abs cta-btn">Jetzt beraten lassen</div>
</section>

<section>
  <div class="abs feature-img" role="img" aria-label="Foto: Hauptplatz in Graz mit bunten Häusern und Brunnen"></div>
  <div class="abs arrow" style="left:114px"><svg width="8" height="8" viewBox="0 0 8 8"><path d="M6 0 L1 4 L6 8 Z" fill="#fff"/></svg></div>
  <div class="abs arrow" style="left:543px"><svg width="8" height="8" viewBox="0 0 8 8"><path d="M2 0 L7 4 L2 8 Z" fill="#fff"/></svg></div>
  <h3 class="abs feature-head">Ich bin eine Headline</h3>
  <p class="abs feature-text" style="top:882px">Lorem ipsum dolor sit amet, consetetur sadipscing elitr, sed diam nonumy eirmod tempor invidunt ut labore et dolore magna aliquyam erat, sed diam voluptua. At vero eos et accusam et justo duo dolores et ea rebum.</p>
  <p class="abs feature-text" style="top:920px">Stet clita kasd gubergren, no sea takimata sanctus est Lorem ipsum dolor sit amet.</p>
  <div class="abs price">Preis in €</div>
  <div class="abs btn" style="left:342px;top:980px;width:73px;height:19px;line-height:19px">Jetzt anfragen</div>
</section>

<footer>
  <div class="abs skyline" role="img" aria-label="Illustration: Stadt- und Bergsilhouette"></div>
  <div class="abs footer"></div>
  <svg class="abs" style="left:128px;top:1103px" width="6" height="8" viewBox="0 0 6 8"><path d="M3 0 A3 3 0 0 1 6 3 C6 5 3 8 3 8 C3 8 0 5 0 3 A3 3 0 0 1 3 0 Z" fill="#fff"/><circle cx="3" cy="3" r="1.1" fill="#a51c29"/></svg>
  <div class="abs f-text" style="left:140px;top:1102px"><span class="f-brand">GaumenpfadReisen</span><br>Marlene Vossberg<br>Lindenhofer Str. 12<br>D - 10999 Berlin</div>
  <svg class="abs" style="left:128px;top:1143px" width="7" height="7" viewBox="0 0 7 7"><path d="M1 0 L2.5 0 L3 2 L2 2.8 C2.5 4 3 4.5 4.2 5 L5 4 L7 4.5 L7 6 C7 6.6 6.5 7 6 7 C3 7 0 4 0 1 C0 0.5 0.4 0 1 0 Z" fill="#fff"/></svg>
  <div class="abs f-text" style="left:140px;top:1142px">Deutschland: +49 170 2836 441<br>Österreich: +43 681 3914 2087</div>

  <div class="abs f-col" style="left:260px;top:1104px;color:#fff">
    <h4>MENÜ</h4><p>MENÜPUNKT</p><p>MENÜPUNKT</p><p>MENÜPUNKT</p><p>MENÜPUNKT</p>
  </div>
  <div class="abs f-col" style="left:339px;top:1104px;color:#fff">
    <h4>MENÜ</h4><p>MENÜPUNKT</p><p>MENÜPUNKT</p><p>MENÜPUNKT</p><p>MENÜPUNKT</p>
  </div>

  <div class="abs social" style="left:416px"></div>
  <div class="abs social" style="left:452px"></div>
  <div class="abs social" style="left:487px"></div>
  <div class="abs social" style="left:522px"></div>

  <div class="abs f-rule"></div>
  <p class="abs copy">© 2017. Agentur Brendl</p>
</footer>

</body>
</html>
```